Business Card for Field Lotus-Eco Friendly Organic Clothing Brand

We are looking for an amazing business card for our eco friendly, organic clothing brand. We are thinking maybe a business card with a peel off sticker on the back, since our hanging clothing tag is a peel off sticker on the back. I will attach our hang tag so we can make sure we stay in line with our design. I've also attached a bag we are doing because I do like the scattered emblem look as well.

```html
<!DOCTYPE html>
<html lang="en">
<head>
<meta charset="utf-8">
<title>Field Lotus — Business Card</title>
<link rel="stylesheet" href="https://fonts.googleapis.com/css2?family=Arimo:wght@400;700&family=Tinos:wght@400&display=swap">
<style>
  :root {
    --backdrop: #d9d2c5;
    --card-black: #0b0b0b;
    --card-sheen: #1c1c1c;
    --brand-pink: #e0128f;
    --brand-green: #1f8a4c;
    --leaf-green: #8a9a6a;
    --ink-white: #f4f4f4;
    --rule-grey: #8c8c8c;
  }
  * { box-sizing: border-box; margin: 0; padding: 0; }
  html, body {
    width: 1200px; height: 892px; overflow: hidden;
    background: var(--backdrop);
    font-family: "Arimo", Arial, sans-serif;
  }
  .stage {
    width: 1200px; height: 892px;
    display: flex; flex-direction: column;
    align-items: center; justify-content: center; gap: 32px;
  }
  .card {
    position: relative;
    width: 700px; height: 400px;
    background: linear-gradient(135deg, var(--card-sheen) 0%, var(--card-black) 55%);
    box-shadow: 0 10px 24px rgba(0,0,0,.25);
    overflow: hidden;
  }
  .card__band {
    position: absolute; left: 0; right: 0; bottom: 0;
    height: 52px;
    background: var(--brand-pink);
    border-top: 5px solid var(--brand-green);
  }

  /* brand mark */
  .brand-mark {
    position: absolute; left: 36px; top: 150px;
    display: flex; align-items: center; gap: 12px;
    white-space: nowrap;
  }
  .brand-mark__dot {
    flex: none;
    width: 40px; height: 40px; border-radius: 50%;
    background: var(--leaf-green);
  }
  .brand-mark__name {
    font-family: "Arimo", Arial, sans-serif;
    font-weight: 700; font-size: 34px; line-height: 1;
    color: var(--brand-pink);
  }

  /* front details */
  .details {
    position: absolute; left: 332px; top: 62px; width: 340px;
  }
  .details__name {
    font-family: "Tinos", Georgia, serif;
    font-weight: 400;
    font-size: 38px; color: var(--brand-green); line-height: 1.05;
  }
  .details__title {
    font-weight: 700; font-size: 22px; color: var(--ink-white);
    margin-top: 2px;
  }
  .details__rule {
    height: 1px; background: var(--rule-grey);
    margin: 14px 0 16px -32px; width: 372px;
  }
  .contact { list-style: none; }
  .contact__item {
    display: flex; align-items: center; gap: 12px;
    font-size: 19px; color: var(--ink-white);
    margin-bottom: 10px; white-space: nowrap;
  }
  .contact__icon {
    width: 22px; height: 22px; flex: none;
    background: var(--ink-white); border-radius: 3px;
    display: flex; align-items: center; justify-content: center;
  }
  .contact__icon svg { width: 16px; height: 16px; }

  /* back */
  .card--back .brand-mark {
    left: 50%; top: 50%; transform: translate(-50%, -62%);
    gap: 22px;
  }
  .card--back .brand-mark__dot {
    width: 76px; height: 76px; background: var(--ink-white);
  }
  .card--back .brand-mark__name {
    font-size: 78px; color: var(--ink-white);
  }
</style>
</head>
<body>
<main class="stage">

  <section class="card card--front" aria-label="Business card front">
    <div class="brand-mark">
      <span class="brand-mark__dot" aria-hidden="true"></span>
      <span class="brand-mark__name">Field Lotus</span>
    </div>

    <div class="details">
      <h1 class="details__name">Dana Reyes</h1>
      <p class="details__title">Managing Director</p>
      <div class="details__rule"></div>
      <ul class="contact">
        <li class="contact__item">
          <span class="contact__icon"><svg viewBox="0 0 16 16"><path d="M4 2l2.5 3-1.5 1.5a8 8 0 0 0 4.5 4.5L11 9.5l3 2.5-1.5 2C7 14 2 9 2 3.5z" fill="#0b0b0b"/></svg></span>
          (800) 555-0142
        </li>
        <li class="contact__item">
          <span class="contact__icon"><svg viewBox="0 0 16 16"><path d="M8 1.5a4.5 4.5 0 0 0-4.5 4.5C3.5 9.5 8 14.5 8 14.5s4.5-5 4.5-8.5A4.5 4.5 0 0 0 8 1.5z" fill="#0b0b0b"/><circle cx="8" cy="6" r="1.6" fill="#f4f4f4"/></svg></span>
          Seabrook, FL&nbsp; 33012
        </li>
        <li class="contact__item">
          <span class="contact__icon"><svg viewBox="0 0 16 16" fill="none" stroke="#0b0b0b" stroke-width="1.4"><circle cx="8" cy="8" r="6"/><ellipse cx="8" cy="8" rx="2.6" ry="6"/><path d="M2 8h12"/></svg></span>
          www.fieldlotus.com
        </li>
        <li class="contact__item">
          <span class="contact__icon"><svg viewBox="0 0 16 16" fill="none" stroke="#0b0b0b" stroke-width="1.4"><rect x="2" y="4" width="12" height="8"/><path d="M2 4l6 5 6-5"/></svg></span>
          hello@fieldlotus.com
        </li>
      </ul>
    </div>

    <div class="card__band"></div>
  </section>

  <section class="card card--back" aria-label="Business card back">
    <div class="brand-mark">
      <span class="brand-mark__dot" aria-hidden="true"></span>
      <span class="brand-mark__name">Field Lotus</span>
    </div>
    <div class="card__band"></div>
  </section>

</main>
</body>
</html>
```